Business card design for a dynamic IT consulting company

We need a business card design for a young firm, specialized in the Telecommunications/Consulting industry. The name of the company is Quindor and Partners Business Consulting Ltd. (Short name: Quindor and Partnes)
Quindor = solve read reverse, so we aim to be uncomplicated and solution-oriented. The small pipe in our logo is also related to the word solve. So we need a new business card design, which is simple, eye catching and something non traditional (I would probably prefer a square shaped design rather than a rectangle, but open for suggestions). Attached our logo.

Target Market(s)

Usually our customers are Tier1 Telecoms providers (Q-Netra, Palorix, etc) and their executives.

Industry/Entity Type

Business

Contact Information for Business Card

Name: Bence Tolnavari
Email: b.tolnavari@quindor.hu
Web: www.quindor.hu
Mobile: +36 30 518 2769
Title: Managing Director

Optional:
Company name: Quindor and Partners Ltd.
Address: 1087 Budapest, Tolvenka str. 28/C, Hungary

Font styles to use
Other font styles liked:
• helveticaneue_medium, Prime Regular are used now.

Colors

Designer to choose colors to be used in the design.

Requirements
Must have
• I would like to have a 2 sided design.
Nice to have
• I thought if we make the logo a bit bigger (without the company name), that could go to the back with the company name below. I though, if the pipe in the logo is somehow touchable on the business card, would be nice and unique.

```html
<!DOCTYPE html>
<html lang="en">
<head>
<meta charset="utf-8">
<title>Quindor and Partners – Business Card</title>
<link href="https://fonts.googleapis.com/css2?family=Oswald:wght@500&family=Work+Sans:wght@400&family=Exo+2:wght@400&display=swap" rel="stylesheet">
<style>
  :root {
    --backdrop: #141414;
    --card: #222222;
    --card-edge: #2c2c2c;
    --brand-grey: #7a7a7a;
    --accent-blue: #1e9ad6;
    --accent-pink: #c2348f;
    --text-light: #e8e8e8;
  }
  * { margin: 0; padding: 0; box-sizing: border-box; }
  html, body {
    width: 1200px; height: 897px; overflow: hidden;
    background: var(--backdrop);
  }
  .canvas { position: relative; width: 1200px; height: 897px; }
  .card {
    position: absolute; left: 303px; width: 594px; height: 338px;
    border-radius: 22px;
    background: linear-gradient(135deg, var(--card) 0%, var(--card) 55%, var(--card-edge) 100%);
  }
  .card--front { top: 92px; }
  .card--back { top: 470px; }

  .brand {
    position: absolute; left: 0; right: 0;
    display: flex; align-items: center; justify-content: center; gap: 10px;
    font-family: "Work Sans", sans-serif; font-weight: 400;
    color: var(--brand-grey); white-space: nowrap; line-height: 1;
  }
  .brand__square { background: var(--brand-grey); flex: none; }
  .card--front .brand { top: 96px; font-size: 22px; }
  .card--front .brand__square { width: 16px; height: 16px; }
  .card--back .brand { top: 152px; font-size: 28px; }
  .card--back .brand__square { width: 20px; height: 20px; }

  .person {
    position: absolute; top: 204px; right: 292px; text-align: right;
  }
  .person__name {
    font-family: "Oswald", sans-serif; font-weight: 500;
    font-size: 30px; line-height: 1; color: var(--accent-blue);
    letter-spacing: 0.2px; transform: scaleX(0.85); transform-origin: right;
    white-space: nowrap;
  }
  .person__title {
    margin-top: 10px;
    font-family: "Work Sans", sans-serif; font-size: 14px;
    color: var(--text-light); letter-spacing: 0.6px; white-space: nowrap;
  }
  .divider {
    position: absolute; left: 326px; top: 198px; width: 2px; height: 56px;
    background: var(--accent-pink);
  }
  .contacts {
    position: absolute; left: 350px; top: 199px; list-style: none;
    font-family: "Work Sans", sans-serif; font-size: 14px;
    color: var(--text-light); letter-spacing: 0.3px; white-space: nowrap;
  }
  .contacts li { display: flex; align-items: center; gap: 10px; height: 19.5px; }
  .contacts svg { width: 12px; height: 12px; fill: var(--accent-blue); flex: none; }

  .company {
    position: absolute; left: 0; right: 0; top: 278px; text-align: center;
  }
  .company__name {
    font-family: "Exo 2", sans-serif; font-weight: 400; font-size: 15px;
    color: var(--accent-blue); letter-spacing: 0.2px;
  }
  .company__address {
    margin-top: 2px;
    font-family: "Work Sans", sans-serif; font-size: 13px;
    color: var(--text-light); letter-spacing: 0.3px;
  }
</style>
</head>
<body>
<div class="canvas">
  <section class="card card--front">
    <div class="brand"><span class="brand__square"></span><span>Quindor</span></div>
    <div class="person">
      <div class="person__name">BENCE TOLNAVARI</div>
      <div class="person__title">MANAGING DIRECTOR</div>
    </div>
    <div class="divider"></div>
    <ul class="contacts">
      <li>
        <svg viewBox="0 0 24 24" aria-hidden="true"><path d="M6.6 10.8a15.1 15.1 0 0 0 6.6 6.6l2.2-2.2c.3-.3.7-.4 1-.2 1.1.4 2.3.6 3.6.6.6 0 1 .4 1 1V20c0 .6-.4 1-1 1A17 17 0 0 1 3 4c0-.6.4-1 1-1h3.5c.6 0 1 .4 1 1 0 1.3.2 2.5.6 3.6.1.3 0 .7-.2 1z"/></svg>
        <span>+36 30 518 2769</span>
      </li>
      <li>
        <svg viewBox="0 0 24 24" aria-hidden="true"><path d="M2 5h20v2l-10 7L2 7z"/><path d="M2 9l10 7 10-7v10H2z"/></svg>
        <span>b.tolnavari@quindor.hu</span>
      </li>
      <li>
        <svg viewBox="0 0 24 24" aria-hidden="true"><circle cx="12" cy="12" r="9.5" fill="none" stroke="#1e9ad6" stroke-width="2"/><ellipse cx="12" cy="12" rx="4" ry="9.5" fill="none" stroke="#1e9ad6" stroke-width="2"/><path d="M3 12h18M5 7h14M5 17h14" stroke="#1e9ad6" stroke-width="1.6"/></svg>
        <span>www.quindor.hu</span>
      </li>
    </ul>
  </section>

  <section class="card card--back">
    <div class="brand"><span class="brand__square"></span><span>Quindor</span></div>
    <div class="company">
      <div class="company__name">QUINDOR AND PARTNERS LTD:</div>
      <div class="company__address">1087 Budapest, Tolvenka str. 28/C, Hungary</div>
    </div>
  </section>
</div>
</body>
</html>
```